Business card design Needed for new logo / Construction business, home extensions and new builds

We need a business card design using our new logo files which i will attach to this project :)

We are a small construction business specialising in home extensions, new builds and property development. We are very ambitious and would appreciate professional and elegant designs for our new business card.

Very serious about using the services on MakerQuarry and recently acquired our new logo from here :)

Please get involved, i will feedback when i can as i am very busy but can respond daily, thanks

Target Market(s)

People that want to build onto their houses, new building developments or adding too their existing property

Industry/Entity Type

Construction

Contact Information for Business Card

Renwick Tolliver Construction, Lionel Ashby (Managing Director), Tel 07822254961, email - info@renwick-tolliver, www.renwick-tolliver.co.uk

Colors

Designer to choose colors to be used in the design.

Requirements
Must have
• I like a deep grey on the back please. A lot of you have provided black from and back, try mixing things up a little. The black looks cool 😎 Thanks

```html
<!DOCTYPE html>
<html lang="en">
<head>
<meta charset="utf-8">
<title>Renwick Tolliver Construction – Business Card</title>
<link rel="stylesheet" href="https://fonts.googleapis.com/css2?family=Arimo:wght@400;700&family=Cinzel:wght@500&display=swap">
<style>
  :root {
    --page: #1e1e20;
    --deep-grey: #2e2e30;
    --gold-dark: #b8852f;
    --gold-mid: #d9ac5c;
    --gold-light: #ecca86;
    --silver: #c9cbcf;
    --ink: #1d1a15;
  }
  * { margin: 0; padding: 0; box-sizing: border-box; }
  html, body { width: 1200px; height: 960px; overflow: hidden; }
  body {
    background: var(--page);
    display: flex;
    flex-direction: column;
    align-items: center;
    justify-content: center;
    gap: 50px;
  }
  .card {
    position: relative;
    width: 700px;
    height: 400px;
    border-radius: 26px;
    overflow: hidden;
    box-shadow: 0 14px 30px rgba(0,0,0,.45);
  }
  .card--back {
    background: var(--deep-grey);
    display: flex;
    align-items: center;
    justify-content: center;
  }
  .card--front {
    background: linear-gradient(120deg, var(--gold-dark) 0%, var(--gold-mid) 35%, var(--gold-light) 60%, var(--gold-mid) 100%);
  }
  .front-panels { position: absolute; inset: 0; }
  .company-name {
    font-family: "Cinzel", serif;
    font-weight: 500;
    color: var(--silver);
    text-align: center;
    letter-spacing: 2px;
    line-height: 1.25;
  }
  .card--back .company-name { font-size: 34px; }
  .card--front .company-name {
    position: absolute;
    left: 400px;
    right: 20px;
    top: 165px;
    font-size: 24px;
  }
  .holder {
    position: absolute;
    left: 44px;
    top: 40px;
    font-family: "Arimo", sans-serif;
    color: var(--ink);
  }
  .holder__name { font-size: 28px; font-weight: 700; }
  .holder__role { font-size: 16px; font-weight: 400; margin-top: 2px; }
  .contact {
    position: absolute;
    left: 44px;
    top: 250px;
    list-style: none;
    font-family: "Arimo", sans-serif;
    font-size: 18px;
    color: var(--ink);
  }
  .contact li { display: flex; align-items: center; gap: 10px; height: 28px; }
  .contact svg { width: 15px; height: 15px; fill: var(--ink); flex: none; }
</style>
</head>
<body>

  <section class="card card--back" aria-label="Card back">
    <p class="company-name">Renwick Tolliver<br>Construction</p>
  </section>

  <section class="card card--front" aria-label="Card front">
    <svg class="front-panels" viewBox="0 0 700 400" width="700" height="400" aria-hidden="true">
      <polygon points="492,0 700,0 700,400 370,400 278,198" fill="var(--deep-grey)"/>
      <polygon points="502,0 700,0 700,400 382,400 292,202" fill="var(--silver)"/>
      <polygon points="516,0 700,0 700,400 398,400 310,206" fill="var(--deep-grey)"/>
    </svg>

    <div class="holder">
      <p class="holder__name">Lionel Ashby</p>
      <p class="holder__role">Managing Director</p>
    </div>

    <ul class="contact">
      <li>
        <svg viewBox="0 0 16 16"><path d="M3.6 1l2.4 2.6-1.4 2a9 9 0 0 0 5 5l2-1.4L14.2 12l-1.6 2.4C7 14.6 1.4 9 1.2 3.2z"/></svg>
        07822254961
      </li>
      <li>
        <svg viewBox="0 0 16 16"><path d="M1 3h14v1.2L8 9 1 4.2z M1 5.8l7 4.8 7-4.8V13H1z"/></svg>
        info@renwick-tolliver
      </li>
      <li>
        <svg viewBox="0 0 16 16"><circle cx="8" cy="8" r="7"/><path d="M4 6h8M3 10h10M8 1c-3 4-3 10 0 14M8 1c3 4 3 10 0 14" stroke="#d9ac5c" stroke-width="1" fill="none"/></svg>
        www.renwick-tolliver.co.uk
      </li>
    </ul>

    <p class="company-name">Renwick Tolliver<br>Construction</p>
  </section>

</body>
</html>
```